Tolbek cards

I want a simple business card that pops.
Logo on one side.
On side two i want.
"Are you thinking about a new building on your property, or renovating an existing structure? Contact".....
Owners Name: Dale Whitacre
Owners Phone number: 610-555-0187
Address:4076 Copper Ridge RD, Marrow Glen, OH 45999
Committed to Quality, Service, and Integrity

```html
<!DOCTYPE html>
<html lang="en">
<head>
<meta charset="utf-8">
<title>Tolbek Builders LLC – Business Card</title>
<link rel="stylesheet" href="https://fonts.googleapis.com/css2?family=Roboto:wght@400;500;700&family=Varela+Round&display=swap">
<style>
  :root {
    --page-bg: #f0f0f0;
    --card-white: #ffffff;
    --brand-dark: #3f2b1c;
    --band-light: #a08d74;
    --band-mid: #7c634b;
    --band-deep: #5a3b24;
    --text-light: #f4f1ec;
  }
  * { box-sizing: border-box; margin: 0; padding: 0; }
  html, body {
    width: 1200px; height: 990px; overflow: hidden;
    background: var(--page-bg);
    font-family: "Roboto", Arial, sans-serif;
  }
  .canvas { position: relative; width: 1200px; height: 990px; }
  .card {
    position: absolute; left: 244px; width: 712px; height: 406px;
    border-radius: 34px; overflow: hidden;
    box-shadow: 0 10px 26px rgba(0,0,0,0.28);
  }
  .card-front { top: 68px; background: var(--card-white); }
  .brand-mark {
    position: absolute; left: 301px; top: 84px;
    width: 110px; height: 110px; background: var(--brand-dark);
  }
  .brand-name { color: var(--brand-dark); font-weight: 700; text-align: center; line-height: 1; }
  .brand-name .brand-main {
    position: absolute; left: 0; right: 0; top: 229px;
    font-size: 88px; letter-spacing: 2px;
  }
  .brand-name .brand-sub {
    position: absolute; left: 0; right: 0; top: 312px;
    font-size: 34px; letter-spacing: 3px;
  }

  .card-back { top: 516px; background: var(--brand-dark); color: var(--text-light); }
  .tagline-band {
    height: 72px; display: flex; align-items: center; justify-content: center;
    font-size: 18px; font-weight: 500; letter-spacing: 0.6px; padding-top: 10px;
  }
  .contact-band {
    height: 243px;
    background: linear-gradient(to bottom, var(--band-light), var(--band-mid) 45%, var(--band-deep));
    position: relative; text-align: center;
  }
  .owner-name {
    position: absolute; left: 0; right: 0; top: 57px;
    font-size: 42px; font-weight: 500; letter-spacing: 0.8px; line-height: 1;
  }
  .owner-role {
    position: absolute; left: 0; right: 0; top: 98px;
    font-family: "Varela Round", Arial, sans-serif; font-size: 19px; letter-spacing: 0.8px; line-height: 1;
  }
  .contact-divider { position: absolute; left: 196px; top: 120px; }
  .contact-phone {
    position: absolute; left: 0; right: 0; top: 154px;
    font-size: 18px; font-weight: 500; letter-spacing: 1.5px; line-height: 1;
  }
  .contact-address {
    position: absolute; left: 0; right: 0; top: 179px;
    font-size: 19px; font-weight: 500; letter-spacing: 1px; line-height: 1;
  }
  .pitch-band {
    height: 91px; display: flex; align-items: center; justify-content: center;
    text-align: center; font-size: 19px; font-weight: 500; letter-spacing: 0.6px; line-height: 26px;
    padding: 0 20px 12px;
  }
</style>
</head>
<body>
<main class="canvas">
  <section class="card card-front" aria-label="Card front">
    <div class="brand-mark"></div>
    <h1 class="brand-name"><span class="brand-main">TOLBEK</span><span class="brand-sub">BUILDERS LLC</span></h1>
  </section>

  <section class="card card-back" aria-label="Card back">
    <div class="tagline-band">Committed to Quality, Service, and Integrity</div>
    <div class="contact-band">
      <h2 class="owner-name">Dale Whitacre</h2>
      <p class="owner-role">Owners</p>
      <svg class="contact-divider" width="320" height="30" viewBox="0 0 320 30" aria-hidden="true">
        <g fill="#f4f1ec">
          <circle cx="18" cy="15" r="2.9"/><circle cx="35" cy="15" r="3.4"/><circle cx="52" cy="15" r="4"/>
          <circle cx="69" cy="15" r="4.6"/><circle cx="86" cy="15" r="5.1"/><circle cx="104" cy="15" r="6"/>
          <circle cx="120" cy="15" r="6.8"/>
          <circle cx="148" cy="14" r="12.5"/><circle cx="180" cy="14" r="12.5"/>
          <circle cx="207" cy="15" r="6.8"/><circle cx="224" cy="15" r="6"/><circle cx="241" cy="15" r="5.1"/>
          <circle cx="258" cy="15" r="4.6"/><circle cx="275" cy="15" r="4"/><circle cx="292" cy="15" r="3.4"/>
          <circle cx="309" cy="15" r="2.9"/>
        </g>
        <path d="M142 8 l3 -1 l2 4 l-2 1.5 q1.5 3.5 5 5 l1.5 -2 l4 2 l-1 3 q-7 1 -12.5 -12.5z" fill="#3f2b1c"/>
        <path d="M150 9 q3 0 4 4 M151 6 q5 1 6 6" stroke="#3f2b1c" stroke-width="1.2" fill="none"/>
        <path d="M180 22 q-6 -7 -6 -11 a6 6 0 0 1 12 0 q0 4 -6 11z" fill="none" stroke="#3f2b1c" stroke-width="1.6"/>
        <circle cx="180" cy="11" r="2" fill="#3f2b1c"/>
        <path d="M175 23 h10" stroke="#3f2b1c" stroke-width="1.4"/>
      </svg>
      <p class="contact-phone">610-555-0187</p>
      <p class="contact-address">4076 Copper Ridge RD, Marrow Glen, OH 45999</p>
    </div>
    <p class="pitch-band">"Are you thinking about a new building on your property, or renovating an<br>existing structure? Contact".....</p>
  </section>
</main>
</body>
</html>
```